Luxury Japanese Matcha Green Tea Packaging Full Packet Design

We're looking for a quality full pack design (front and back) for Ceremonial Grade and Premium Grade Matcha to sell on Bazaarly. We need a 2D versions of front and back images in photoshop and JPG. We also need a 3D versions of front and back for marketing purposes.

You can see our current styling and pack at www.brewvantis.co.uk. However, we want to improve the design and go more professional, simple and elegant with the brand. The last design was from 3 years a go. But hopefully you can see what we are about.

The design will be identical both both packs:

Pack 1: 230mm x 140mm - Premium Grade
Pack 2: 170mm x 120mm - Ceremonial Grade

The design needs to fit both sizes, with pack 1 saying Premium Grade and pack 2 saying Ceremonial Grade.

As many colours as needed, printing is CMYK + White digital printed.

Front of pack:

Product Headline:

Organic Handpicked
Stoneground Japanese Matcha
Green Tea Powder

抹茶

Text: Premium Grade (pack 1) / Ceremonial Grade (pack 2)

100g (pack 1) / 40g (pack 2)

(EU Organic logo)

Back of pack:

Organic Certified GB-ORG-19
Stone Ground Ceremonial Grade Matcha from Uji

Ingredients: 100% Organic Matcha Green Tea Powder

Place of origin: Japan, Store in a cool, dry, dark place
Keep sealed at all times, Best Before 31/03/2020
Not recommended for use if pregnant or nursing

Your next order is ready for you at www.KelpHour.co.uk

Preparing Traditional Matcha Tea:
Sift 1-2g or 1/2 teaspoon of Matcha Green Tea
powder into a bowl or large cup. Add 1/2 cup of hot water
at drinking temperature. Whisk with Bamboo or
Electric Whisk until frothy. Drink immediately.

Preparing Matcha Latte:
Sift 1-2g of Matcha Power into a cup, mix in 2-3 tablespoons of hot water.
Add hot milk and sweetener if desired. Whisk thoroughly.

Nutritional Information:

Per 1g Per 100g
Energy 14.44kJ 1446kJ
3.44kCal 345kCal
Fat 0.04g 4g
Saturates <0.01g 0.6g
Carbohydrates 0.76g 76g
of which sugars 0.47g 47.2g
Protein 0.144g 14.5g
Salt <0.01g 126mg

Per 1g Per 100g
Calcium 1.88mg 191mg
Potassium 94.8mg 3750mg
Iron <0.1g 1.6mg
Zinc <0.1g 1.72mg
Vitamin A 120µg (15% RDA) 2400µg (150% RDA)
Vitamin C 3mg (4% RDA) 60mg (75% RDA)
Folic acid 6µg (6% RDA) 60µg (30% RDA)
Riboflavin 0.1mg (4% RDA) 1.4mg (96% RDA)
Caffeine 17mg 1700mg

Quillon Harbour Ltd. T/A Brewvantis
Company Number: 05617429
Registered Office: 7 The Yard, Darnwick Cl
Newbury, Berkshire, RG17 2QH
social@brewvantis.co.uk
Local Call +44 (0) 20 3184 6057 / Freephone +44 (0) 800 512 7736

This supplement should not be used as a substitute for a varied diet Do not exceed the recommended daily dose.

For more information on Matcha, download the free eBook at www.TheLeafPrimer.com

Please consult a healthcare practitioner if you are pregnant or taking prescription medicine before using this product.

Recommended daily dose

1-5g daily

Storage information: Store in a cool dry place away from sunlight, moisture, and heat. Keep contents dry.

Logos for back of pack:
EU Organic logo with 'GB-ORG-19 Non-EU Agriculture' written directly underneath it.
Vegan logo
Natural Crop Alliance logo
Bazaarly Barcode

Additional deisgn notes:

We have included a design that we like.

The top 2cm will be torn off by the user, so should not contain any key information.

Target Market(s)

High End health and wellness Consumers

Colors
acd036
0455a3
edf8f6

Requirements
Must have
• Stand out on Bazaarly. Show the product to be premium.

```html
<!DOCTYPE html>
<html lang="en">
<head>
<meta charset="utf-8">
<title>Stoneground Japanese Matcha – Front of Pack</title>
<link href="https://fonts.googleapis.com/css2?family=Kaushan+Script&family=Open+Sans:wght@600;700&family=Roboto+Condensed:wght@400;700&family=Noto+Serif+JP:wght@400&display=swap" rel="stylesheet">
<style>
  :root {
    --stage: #e4e5e4;
    --pack-white: #fbfbfa;
    --pattern-tint: #f1f2ef;
    --lime: #acd036;
    --leaf-dark: #5b7a1c;
    --leaf-mid: #7fa52a;
    --band-dark: #3b3b3b;
    --ink: #2b2b2b;
    --photo-light: #cfcfcf;
    --photo-dark: #6a6a6a;
  }
  html, body {
    margin: 0;
    padding: 0;
    width: 1200px;
    height: 1115px;
    overflow: hidden;
    background: var(--stage);
  }
  .canvas {
    position: relative;
    width: 1200px;
    height: 1115px;
  }
  .pack {
    position: absolute;
    left: 290px;
    top: 86px;
    width: 620px;
    height: 944px;
    background: var(--pack-white);
    overflow: hidden;
  }
  .pack__pattern {
    position: absolute;
    left: 0; top: 232px;
    width: 620px; height: 712px;
    background: var(--pattern-tint);
  }
  .pack__landscape {
    position: absolute;
    left: 0; top: 0;
    width: 620px; height: 232px;
    background: linear-gradient(180deg, var(--photo-light) 0%, #a9a9a9 45%, var(--photo-dark) 100%);
  }
  .pack__cert-corner {
    position: absolute;
    left: 0; top: 0;
  }
  .headline-band {
    position: absolute;
    left: 148px; top: 156px;
    width: 342px; height: 70px;
    background: var(--band-dark);
    color: #fff;
    font-family: "Kaushan Script", cursive;
    font-size: 37px;
    line-height: 70px;
    text-align: center;
    margin: 0;
    font-weight: 400;
  }
  .origin-badge {
    position: absolute;
    left: 170px; top: 226px;
    width: 297px; height: 134px;
    background: var(--lime);
    border-radius: 0 0 150px 150px / 0 0 120px 120px;
    color: var(--leaf-dark);
    font-family: "Kaushan Script", cursive;
    text-align: center;
    font-size: 40px;
    line-height: 44px;
    padding-top: 4px;
    box-sizing: border-box;
  }
  .origin-badge span { display: block; }
  .heart {
    position: absolute;
    left: 154px; top: 356px;
    width: 376px; height: 330px;
  }
  .heart__title {
    position: absolute;
    left: 154px; top: 420px;
    width: 376px;
    text-align: center;
    font-family: "Kaushan Script", cursive;
    font-size: 86px;
    line-height: 100px;
    color: var(--leaf-mid);
    margin: 0;
    font-weight: 400;
  }
  .heart__kanji {
    position: absolute;
    left: 154px; top: 524px;
    width: 376px;
    text-align: center;
    font-family: "Noto Serif JP", serif;
    font-size: 54px;
    line-height: 64px;
    color: var(--ink);
  }
  .product-type {
    position: absolute;
    left: 88px; top: 714px;
    width: 450px; height: 68px;
    box-sizing: border-box;
    border: 2px solid var(--leaf-dark);
    background: var(--pack-white);
    font-family: "Open Sans", sans-serif;
    font-weight: 700;
    font-size: 23px;
    letter-spacing: 8px;
    color: var(--leaf-dark);
    text-align: center;
    line-height: 64px;
  }
  .divider-stem {
    position: absolute;
    left: 321px; top: 782px;
    width: 2px; height: 108px;
    background: var(--leaf-dark);
  }
  .divider-foot {
    position: absolute;
    left: 266px; top: 889px;
    width: 113px; height: 2px;
    background: var(--leaf-dark);
  }
  .grade {
    position: absolute;
    left: 87px; top: 820px;
    font-family: "Open Sans", sans-serif;
    font-weight: 700;
    font-size: 23px;
    letter-spacing: 1.5px;
    color: var(--ink);
  }
  .certification {
    position: absolute;
    left: 382px; top: 821px;
    display: flex;
    align-items: center;
    gap: 8px;
  }
  .certification__mark {
    width: 40px; height: 30px;
    background: var(--lime);
  }
  .certification__text {
    font-family: "Roboto Condensed", sans-serif;
    font-size: 13px;
    line-height: 16px;
    color: var(--ink);
    text-transform: uppercase;
  }
  .net-weight {
    position: absolute;
    left: 236px; top: 893px;
    width: 172px;
    text-align: center;
    font-family: "Roboto Condensed", sans-serif;
    font-size: 16px;
    color: var(--ink);
  }
</style>
</head>
<body>
<main class="canvas">
  <section class="pack" aria-label="Matcha pouch front">
    <div class="pack__pattern" role="img" aria-label="Faint line-drawn pattern of tea bowls, whisks and teapots"></div>
    <div class="pack__landscape" role="img" aria-label="Black and white photograph of terraced tea fields"></div>
    <svg class="pack__cert-corner" width="92" height="92" viewBox="0 0 92 92" aria-hidden="true">
      <path d="M0 0 H92 L0 92 Z" fill="#3f4a2a"/>
      <circle cx="28" cy="28" r="15" fill="none" stroke="#ffffff" stroke-width="1.5"/>
    </svg>

    <h1 class="headline-band">Organic Handpicked</h1>
    <div class="origin-badge"><span>Stoneground</span><span>Japanese</span></div>

    <svg class="heart" viewBox="0 0 100 88" role="img" aria-label="Heart of fresh matcha powder">
      <defs>
        <radialGradient id="powder" cx="50%" cy="45%" r="60%">
          <stop offset="0%" stop-color="#9cc53a"/>
          <stop offset="100%" stop-color="#6f9a25"/>
        </radialGradient>
      </defs>
      <path d="M50 87 C20 64 0 46 0 26 C0 10 12 0 26 0 C37 0 45 7 50 16 C55 7 63 0 74 0 C88 0 100 10 100 26 C100 46 80 64 50 87Z" fill="url(#powder)"/>
      <path transform="translate(50 44) scale(0.8) translate(-50 -44)" d="M50 87 C20 64 0 46 0 26 C0 10 12 0 26 0 C37 0 45 7 50 16 C55 7 63 0 74 0 C88 0 100 10 100 26 C100 46 80 64 50 87Z" fill="#fbfbfa"/>
    </svg>
    <h2 class="heart__title">Matcha</h2>
    <div class="heart__kanji" lang="ja">抹茶</div>

    <div class="product-type">GREEN TEA POWDER</div>
    <div class="divider-stem"></div>
    <div class="divider-foot"></div>

    <div class="grade">PREMIUM GRADE</div>
    <div class="certification">
      <div class="certification__mark"></div>
      <div class="certification__text">Acquired EU<br>Organic Certification</div>
    </div>

    <div class="net-weight">NET WT. 100G</div>
  </section>
</main>
</body>
</html>
```